Social Media Graphics - Oakline Push REVISED

Create 6-7 individual social media graphics (square size) to encourage folks to join our online course called:

The Harvest Ledger Circle
How to Launch a Multi-Million Business From Scratch
Sign Up Today!

IMPORTANT: Make the largest and most prominent text on the graphic be: How to Launch a Multi-Million Business From Scratch

For the color scheme of the graphics, let's try a blue color palette; make sure the graphics appeal to both men and women

Make sure each graphic contains 1 of the 3 pics attached (crop pic as needed); and make sure one of the graphics is all TEXT only.

Target Market(s)

men and women looking to start a business

Industry/Entity Type

Entrepreneurship

Colors
0054AA
0677BA
7BADD7
CADEEF
E8F1F8

Requirements
Must have
• All the text and use the 3 pics provided; one graphic can be all text; Simple, modern design that's easy to read

```html
<!DOCTYPE html>
<html lang="en">
<head>
<meta charset="UTF-8">
<title>Oakline Push – The Harvest Ledger Circle</title>
<link rel="stylesheet" href="https://fonts.googleapis.com/css2?family=Lilita+One&family=Montserrat:wght@800&display=swap">
<style>
  :root {
    --blue-deep: #0054AA;
    --blue-mid: #0677BA;
    --blue-soft: #7BADD7;
    --blue-pale: #CADEEF;
    --blue-mist: #E8F1F8;
    --white: #FFFFFF;
    --ink: #0B2540;
  }
  * { margin: 0; padding: 0; box-sizing: border-box; }
  html, body { width: 1200px; height: 1200px; overflow: hidden; background: var(--blue-mid); }
  .post {
    position: relative;
    width: 1200px;
    height: 1200px;
    overflow: hidden;
    background: var(--blue-mid);
  }
  .backdrop { position: absolute; inset: 0; width: 1200px; height: 1200px; z-index: 1; }
  .headline {
    position: absolute;
    left: 63px;
    top: 62px;
    width: 820px;
    font-family: "Lilita One", "Arial Black", sans-serif;
    font-weight: 400;
    font-size: 88px;
    line-height: 117px;
    color: var(--white);
    text-transform: uppercase;
    text-shadow: 4px 5px 0 var(--ink);
    letter-spacing: 1.5px;
    white-space: nowrap;
    z-index: 4;
  }
  .course-name {
    position: absolute;
    left: 63px;
    top: 563px;
    font-family: "Lilita One", "Arial Black", sans-serif;
    font-weight: 400;
    font-size: 58px;
    line-height: 83px;
    color: var(--blue-mist);
    text-transform: uppercase;
    text-shadow: 3px 4px 0 var(--ink);
    letter-spacing: 1px;
    white-space: nowrap;
    z-index: 4;
  }
  .cta {
    position: absolute;
    left: 63px;
    top: 791px;
    width: 343px;
    height: 85px;
    border: 5px solid var(--blue-mist);
    display: flex;
    align-items: center;
    justify-content: center;
    font-family: "Montserrat", sans-serif;
    font-weight: 800;
    font-size: 26px;
    color: var(--white);
    text-transform: uppercase;
    z-index: 4;
  }
  .hosts-photo {
    position: absolute;
    left: 490px;
    top: 500px;
    width: 710px;
    height: 700px;
    border-radius: 300px 300px 0 0;
    background: linear-gradient(160deg, #2a2a2e 0%, #1b1b1f 45%, #1d3f78 75%, #24549a 100%);
    z-index: 2;
  }
</style>
</head>
<body>
<main class="post">
  <svg class="backdrop" viewBox="0 0 1200 1200" aria-hidden="true">
    <path class="backdrop-wave" fill="var(--blue-deep)"
      d="M533 0 C600 60 680 120 650 230 C620 330 700 380 790 440 C880 500 880 620 900 760 C930 960 1000 1100 1060 1200 L1200 1200 L1200 0 Z"/>
    <g class="dot-grid" fill="var(--blue-soft)">
      <circle cx="1003" cy="67" r="6"/><circle cx="1053" cy="67" r="6"/>
      <circle cx="1105" cy="67" r="6"/><circle cx="1156" cy="67" r="6"/>
      <circle cx="1003" cy="126" r="6"/><circle cx="1053" cy="126" r="6"/>
      <circle cx="1105" cy="126" r="6"/><circle cx="1156" cy="126" r="6"/>
    </g>
    <circle class="bubble-small" cx="519" cy="436" r="29" fill="var(--blue-pale)"/>
    <circle class="bubble-large" cx="613" cy="511" r="69" fill="var(--blue-mist)"/>
  </svg>

  <h1 class="headline">How to launch a<br>multi-million<br>business from<br>scratch</h1>

  <h2 class="course-name">The Harvest<br>Ledger Circle</h2>

  <div class="cta">Sign up today!</div>

  <div class="hosts-photo" role="img" aria-label="Photo of the two course hosts, a man in a black turtleneck with arms crossed and a woman in a denim blazer, smiling"></div>
</main>
</body>
</html>
```